New Company Business Card design

Looking for a corporate looking business card utilising my new logo design - the logo i would like embossed as one option and flat as another - simplistic but stylish - less is more - we are an import export business launching into the market - i would like a couple of options as main background - Grey or Black

```html
<!DOCTYPE html>
<html lang="en">
<head>
<meta charset="utf-8">
<title>Meridian Trade Partners – Business Card</title>
<link href="https://fonts.googleapis.com/css2?family=Oswald:wght@500&family=Work+Sans:wght@400;500&display=swap" rel="stylesheet">
<style>
  :root {
    --bg: #262626;
    --card: #1b1b1c;
    --blue: #1a78c8;
    --text: #f2f2f2;
  }
  * { margin: 0; padding: 0; box-sizing: border-box; }
  html, body { width: 1200px; height: 900px; overflow: hidden; background: var(--bg); }
  .stage {
    width: 1200px; height: 900px;
    display: flex; flex-direction: column; align-items: center; justify-content: center; gap: 40px;
  }
  .card {
    position: relative;
    width: 660px; height: 380px;
    background: var(--card);
    border-bottom: 6px solid var(--blue);
    box-shadow: 0 14px 30px rgba(0,0,0,.45);
    font-family: "Work Sans", Arial, sans-serif;
    color: var(--text);
    overflow: hidden;
  }
  /* Front */
  .brand {
    position: absolute; inset: 0;
    display: flex; align-items: center; justify-content: center; gap: 14px;
  }
  .brand-dot { width: 22px; height: 22px; border-radius: 50%; background: var(--blue); }
  .brand-name {
    font-size: 30px; font-weight: 500; letter-spacing: 2px; text-transform: uppercase;
    color: var(--blue);
  }
  /* Back */
  .identity {
    position: absolute; left: 60px; top: 150px; width: 250px; text-align: right;
  }
  .person-name {
    font-family: "Oswald", "Arial Narrow", sans-serif;
    font-size: 40px; font-weight: 500; line-height: 1; color: var(--blue); text-transform: uppercase;
    white-space: nowrap;
  }
  .person-role { font-size: 18px; margin-top: 8px; }
  .divider {
    position: absolute; left: 328px; top: 152px; width: 2px; height: 68px; background: var(--blue);
  }
  .contacts {
    position: absolute; left: 348px; top: 150px; list-style: none;
    font-size: 18px; line-height: 26px; letter-spacing: .3px;
  }
  .contacts li { display: flex; align-items: center; gap: 10px; white-space: nowrap; }
  .contacts svg { width: 13px; height: 13px; flex: none; }
  .accent { color: var(--blue); }
  .address {
    position: absolute; left: 100px; bottom: 58px;
    font-size: 18px; letter-spacing: .5px; white-space: nowrap;
  }
</style>
</head>
<body>
<main class="stage">
  <section class="card card-front">
    <div class="brand">
      <span class="brand-dot"></span>
      <span class="brand-name">Meridian Trade Partners</span>
    </div>
  </section>

  <section class="card card-back">
    <div class="identity">
      <div class="person-name">Daniel Harper</div>
      <div class="person-role">Director</div>
    </div>
    <div class="divider"></div>
    <ul class="contacts">
      <li>
        <svg viewBox="0 0 24 24"><path fill="#1a78c8" d="M6.6 10.8a15 15 0 0 0 6.6 6.6l2.2-2.2c.3-.3.7-.4 1-.2 1.1.4 2.3.6 3.6.6.6 0 1 .4 1 1V20c0 .6-.4 1-1 1A17 17 0 0 1 3 4c0-.6.4-1 1-1h3.5c.6 0 1 .4 1 1 0 1.3.2 2.5.6 3.6.1.3 0 .7-.2 1z"/></svg>
        555-014-2277
      </li>
      <li>
        <svg viewBox="0 0 24 24"><rect x="2.5" y="5" width="19" height="14" fill="none" stroke="#1a78c8" stroke-width="2"/><path d="M3 6l9 7 9-7" fill="none" stroke="#1a78c8" stroke-width="2"/></svg>
        info@meridiantrade.com
      </li>
      <li>
        <svg viewBox="0 0 24 24"><circle cx="12" cy="12" r="9.5" fill="none" stroke="#1a78c8" stroke-width="2"/><path d="M2.5 12h19M12 2.5c3 3 3 16 0 19M12 2.5c-3 3-3 16 0 19" fill="none" stroke="#1a78c8" stroke-width="1.6"/></svg>
        <span>www.<span class="accent">meridiantrade</span>.com</span>
      </li>
    </ul>
    <p class="address">2250 Orchard Valley Rd Fairview, CA 95100-4120</p>
  </section>
</main>
</body>
</html>
```